Business Card Design for Vintage Jazz

I am a vintage jazz band leader in New York City. My groups play the music of the 1920s, 1930s and 1940s. My website is morvalquist.com for more info on what I do.

I am looking for a two sided business card design that has the look and feel of a really nice business card from the 1930s. I need to convey with the design that my work has that vintage kind of class and style, but also conveys that we are fun and entertaining.

Most importantly it should make a bold staement. If Hal Denbrook had a card, what would it have looked like? I want a card that I feel confident will make an impact and will let people know that my work is te the top that NYC has to offer in vintage jazz..

Note that I have only decided to avoid the "committed payment" option as I have not used this service before. Assuming that I get quality work I will select a design from those presented.

Target Market(s)

people who want to hire my band for events, media, and new fans of the band

Industry/Entity Type

Performing Art

Contact Information for Business Card

Definitely a matte finish, possibly a sort of old style of paper with that brown tint? definitely a thick card.

Requirements
Must have
• FRONT
• My name: Tobin Vashley
• What I do: Bandleader, Guitarist, Vocalist, Songwriter
• Contact Details: morvalquist.com tobin@morvalquist.com 646-555-0148
• BACK
• My Social Media Links:
• facebook.morvalquist.com
• twitter, instagram, linkedin: morvalquist
• I'm also including a photo image I would like to use. The photo's background is not needed, and to be honest isn't really desireable. Just looking to use the image of me.
Nice to have
• I'm attaching which could be used as is, omitted from the card, or altered maybe with text going around the outside of the circle or in some other way. It may need some clean up to the edges of the lettering as we only use it for the website thumbnail.
• If there's space I'd like to include the text "join our mailing list for a free song download: freesong.morvalquist.com" If not perhaps just "Download a Free Song at: freesong.morvalquist.com - something to this end.
Should not have
• anything cartoony. Don't think retro 90s's vision of the swing era, think actual swing era!
• anything modern. Got to look old school
• Try to avoid dark backgrounds. Since we often play in bars and clubs where it is dar, a d
• avoid script fonts.

```html
<!DOCTYPE html>
<html lang="en">
<head>
<meta charset="utf-8">
<title>Tobin Vashley – Business Card</title>
<link rel="stylesheet" href="https://fonts.googleapis.com/css2?family=Open+Sans:wght@400;600;700;800&display=swap">
<style>
  :root {
    --page: #e6e6e6;
    --card: #ffffff;
    --ink: #111111;
    --band: #6b6b6b;
    --band-text: #ffffff;
    --teal: #5ecbb3;
    --photo-dark: #3a3a3a;
    --rule: #333333;
  }
  * { box-sizing: border-box; margin: 0; padding: 0; }
  html, body {
    width: 1200px; height: 900px; overflow: hidden;
    background: var(--page);
    font-family: "Open Sans", Arial, sans-serif;
    color: var(--ink);
  }
  .canvas { position: relative; width: 1200px; height: 900px; }
  .card {
    position: absolute;
    width: 560px; height: 320px;
    background: var(--card);
    border-radius: 22px;
    box-shadow: 0 10px 30px rgba(0,0,0,.18);
    overflow: hidden;
  }
  .card--back { left: 90px; top: 90px; }
  .card--front { left: 550px; top: 490px; }

  .monogram {
    position: absolute;
    border-radius: 50%;
    background: var(--ink);
    display: flex; align-items: center; justify-content: center;
    color: #fff; font-weight: 700; letter-spacing: .04em;
  }
  .card--back .monogram {
    width: 170px; height: 170px; left: 195px; top: 30px; font-size: 20px;
  }

  .download { position: absolute; left: 34px; bottom: 34px; }
  .download__title { font-weight: 700; font-size: 14.5px; letter-spacing: .05em; text-transform: uppercase; }
  .download__url { margin-top: 10px; font-size: 12.5px; letter-spacing: .02em; }
  .divider {
    position: absolute; left: 296px; bottom: 42px;
    width: 1.5px; height: 42px; background: var(--rule);
  }
  .social { position: absolute; left: 312px; bottom: 40px; font-size: 13px; }
  .social__row { display: flex; align-items: center; gap: 8px; height: 22px; }
  .social__tag { font-weight: 700; font-size: 11px; }
  .social__row + .social__row { margin-top: 4px; }

  .band {
    position: absolute; left: 0; right: 0; top: 108px; height: 118px;
    background: var(--band);
  }
  .card--front .monogram {
    width: 150px; height: 150px; left: 36px; top: 92px; font-size: 17px;
    border: 4px solid #fff;
  }
  .identity {
    position: absolute; left: 205px; top: 112px; width: 230px;
    color: var(--band-text); text-align: right;
  }
  .identity__name { font-weight: 800; font-size: 22px; letter-spacing: .03em; text-transform: uppercase; line-height: 1.1; }
  .identity__role { font-size: 12.5px; text-transform: uppercase; letter-spacing: .03em; line-height: 1.25; }
  .identity__contact { margin-top: 6px; font-size: 12.5px; line-height: 1.3; }
  .identity__contact b { font-weight: 700; }
  .portrait {
    position: absolute; left: 438px; top: 106px;
    width: 116px; height: 116px; border-radius: 50%;
    border: 4px solid #fff;
    background: radial-gradient(circle at 45% 55%, var(--photo-dark) 0 38%, var(--teal) 40%);
  }
</style>
</head>
<body>
<main class="canvas">
  <section class="card card--back" aria-label="Card back">
    <div class="monogram">MORVALQUIST</div>
    <div class="download">
      <p class="download__title">Download a free song at</p>
      <p class="download__url">www.freesong.morvalquist.com</p>
    </div>
    <div class="divider"></div>
    <div class="social">
      <p class="social__row"><span class="social__tag">fb</span> facebook.morvalquist.com</p>
      <p class="social__row"><span class="social__tag">tw · ig · in</span> morvalquist</p>
    </div>
  </section>

  <section class="card card--front" aria-label="Card front">
    <div class="band"></div>
    <div class="monogram">MORVALQUIST</div>
    <div class="identity">
      <h1 class="identity__name">Tobin Vashley</h1>
      <p class="identity__role">Bandleader, Guitarist<br>Vocalist, Songwriter</p>
      <p class="identity__contact">
        <b>P:</b> 646-555-0148<br>
        <b>E:</b> tobin@morvalquist.com<br>
        <b>W:</b> www.morvalquist.com
      </p>
    </div>
    <div class="portrait" role="img" aria-label="Photo of Tobin Vashley in a dark suit tipping a hat, on a teal circle"></div>
  </section>
</main>
</body>
</html>
```